Velvet Lantern rebranding my business with a new business card

I have my new logo and now I need a refresher on my business cards. I really want something fun and fresh. I like black background or anything to make the color pop.
Logo
Name: Velvet Lantern
Contact Info as stated below:
Mira Pellow
555-013-4762
Logo
Name: Velvet Lantern
Mira Pellow
555-013-4762
fb.me/VelvetLanternbyMira
Instagram: @VelvetLanternbyMira

Industry/Entity Type

Business

Contact Information for Business Card

double-sided. Logo on one side. Contact info on the other.

Requirements
Must have
• Logo
• Name: Velvet Lantern
• Contact Info as stated below:
• Mira Pellow
• 555-013-4762
• fb.me/VelvetLanternbyMira
• fb.me/VelvetLanternbyMira

```html
<!DOCTYPE html>
<html lang="en">
<head>
<meta charset="utf-8">
<title>Velvet Lantern – Business Card</title>
<link rel="stylesheet" href="https://fonts.googleapis.com/css2?family=Open+Sans:wght@400;600&family=PT+Serif:wght@400&display=swap">
<style>
  :root {
    --backdrop: #e9e6e3;
    --card: #ffffff;
    --ink: #2a2a2a;
    --ink-soft: #555555;
    --violet: #b24fd0;
    --ring: #e7a9bd;
    --accent-warm: #e48a9c;
    --accent-soft: #f6c9d4;
  }
  * { box-sizing: border-box; margin: 0; padding: 0; }
  html, body { width: 1200px; height: 911px; overflow: hidden; }
  body {
    background: var(--backdrop);
    font-family: "Open Sans", sans-serif;
    color: var(--ink);
    position: relative;
  }
  .card {
    position: absolute;
    width: 520px;
    height: 310px;
    background: var(--card);
    border-radius: 18px;
    overflow: hidden;
    box-shadow: 0 6px 18px rgba(0,0,0,0.18);
  }
  .card--front { left: 45px; top: 300px; }
  .card--back  { left: 635px; top: 300px; }

  .front-swoosh { position: absolute; inset: 0; }

  .brand-badge {
    position: absolute;
    left: 40px; top: 40px;
    width: 140px; height: 140px;
    border-radius: 50%;
    border: 3px solid var(--ring);
    display: flex; align-items: center; justify-content: center;
    text-align: center;
  }
  .brand-name {
    font-family: "Open Sans", sans-serif;
    font-weight: 600;
    font-size: 17px;
    line-height: 1.2;
    color: var(--violet);
  }

  .accent-art {
    position: absolute;
    left: 360px; top: 88px;
    width: 44px; height: 30px;
    border-radius: 6px;
    background: linear-gradient(135deg, var(--accent-warm), var(--accent-soft));
    opacity: 0.85;
  }

  .contact-list {
    position: absolute;
    left: 300px; top: 150px;
    list-style: none;
    font-size: 13px;
    line-height: 22px;
    color: var(--ink);
  }
  .contact-list li { display: flex; align-items: center; gap: 7px; }
  .contact-list svg { width: 12px; height: 12px; flex: none; }

  .person-name {
    position: absolute;
    left: 150px; top: 248px;
    font-family: "PT Serif", serif;
    font-weight: 400;
    font-size: 24px;
    letter-spacing: 0.5px;
    color: #3a1f3f;
  }

  .back-logo {
    position: absolute;
    right: 70px; top: 170px;
    display: flex; align-items: center; gap: 12px;
  }
  .back-logo-mark {
    width: 40px; height: 40px;
    border-radius: 50%;
    border: 3px solid var(--ring);
    flex: none;
  }
  .back-logo .brand-name { font-size: 22px; }
  .back-url {
    position: absolute;
    right: 70px; top: 232px;
    font-size: 13px;
    color: var(--ink-soft);
  }
</style>
</head>
<body>

  <section class="card card--front" aria-label="Card front">
    <svg class="front-swoosh" viewBox="0 0 520 310" preserveAspectRatio="none" aria-hidden="true">
      <defs>
        <linearGradient id="bandFill" x1="0" y1="1" x2="1" y2="0">
          <stop offset="0" stop-color="#a83fd0"/>
          <stop offset="0.35" stop-color="#d98ad0"/>
          <stop offset="0.7" stop-color="#f5bccd"/>
          <stop offset="1" stop-color="#fbe3ea"/>
        </linearGradient>
      </defs>
      <path d="M0 310 L0 300 C120 250 220 120 520 80 L520 310 Z" fill="url(#bandFill)"/>
      <path d="M0 300 C120 250 220 120 520 80" fill="none" stroke="#ffffff" stroke-width="3" opacity="0.8"/>
      <path d="M20 310 C140 240 250 140 520 100" fill="none" stroke="#ffffff" stroke-width="1.5" opacity="0.5"/>
    </svg>

    <div class="brand-badge">
      <span class="brand-name">Velvet<br>Lantern</span>
    </div>

    <div class="accent-art" role="img" aria-label="Small fruit illustration sitting on the swoosh"></div>

    <ul class="contact-list">
      <li>
        <svg viewBox="0 0 12 12" aria-hidden="true"><path d="M2.5 1 L4.5 1 L5.3 3.6 L4 4.6 C4.6 6 5.9 7.3 7.4 8 L8.4 6.7 L11 7.5 L11 9.5 C11 10.3 10.3 11 9.5 11 C5 11 1 7 1 2.5 C1 1.7 1.7 1 2.5 1 Z" fill="#2a2a2a"/></svg>
        555-013-4762
      </li>
      <li>
        <svg viewBox="0 0 12 12" aria-hidden="true"><circle cx="6" cy="6" r="5" fill="none" stroke="#2a2a2a" stroke-width="1.3"/><path d="M1 6 H11 M6 1 C3.5 4 3.5 8 6 11 M6 1 C8.5 4 8.5 8 6 11" fill="none" stroke="#2a2a2a" stroke-width="1"/></svg>
        www.velvetlantern.com
      </li>
      <li>
        <svg viewBox="0 0 12 12" aria-hidden="true"><rect x="1" y="1" width="10" height="10" rx="1.5" fill="#2a2a2a"/></svg>
        fb.me/VelvetLanternbyMira
      </li>
    </ul>

    <h1 class="person-name">MIRA PELLOW</h1>
  </section>

  <section class="card card--back" aria-label="Card back">
    <div class="back-logo">
      <span class="back-logo-mark" aria-hidden="true"></span>
      <span class="brand-name">Velvet Lantern</span>
    </div>
    <span class="back-url">www.velvetlantern.com</span>
  </section>

</body>
</html>
```